New Webpage for High Class Expert Witness Services Company

We are looking for a minimalist design for a webpage that just has our logo and an entry form offer to connect with one of our Liaisons.
The entry form should just ask for Name, Email, Contact Info and Description of Project.

Company Name is: The Marlowe Crest Advisory Services

Number of Pages Required

1 page

```html
<!DOCTYPE html>
<html lang="en">
<head>
<meta charset="utf-8">
<title>The Marlowe Crest Advisory Services — Connect with a Liaison</title>
<link rel="stylesheet" href="https://fonts.googleapis.com/css2?family=Cinzel:wght@600;700&family=Poppins:wght@400&display=swap">
<style>
  :root {
    --bg-dark: #9a9a9f;
    --bg-light: #e6e6e8;
    --brand-text: #eeeef0;
    --panel: #3f3f41;
    --heading: #e2e2e4;
    --heading-sub: #bdbdc0;
    --label: #dcdcde;
    --field: #e4e4e6;
    --field-text: #555a60;
    --placeholder: #8a8e94;
    --icon: #7c8792;
    --button: #000000;
    --button-text: #ffffff;
  }
  * { box-sizing: border-box; margin: 0; padding: 0; }
  html, body { width: 1200px; height: 750px; overflow: hidden; }
  body {
    position: relative;
    background: linear-gradient(160deg, var(--bg-dark) 0%, #b4b4b8 45%, var(--bg-light) 100%);
    font-family: "Poppins", sans-serif;
  }
  .brand {
    position: absolute;
    left: 343px; top: 52px; width: 514px;
    display: flex; align-items: center; justify-content: center; gap: 16px;
  }
  .brand-mark {
    width: 40px; height: 40px; flex: none;
    background: var(--brand-text);
  }
  .brand-name {
    font-family: "Cinzel", serif;
    font-weight: 600;
    font-size: 25px;
    line-height: 1.2;
    letter-spacing: 1px;
    color: var(--brand-text);
    text-transform: uppercase;
  }
  .liaison-panel {
    position: absolute;
    left: 381px; top: 186px; width: 439px; height: 465px;
    background: var(--panel);
    padding: 36px 39px 0;
  }
  .panel-heading {
    font-family: "Cinzel", serif;
    font-weight: 700;
    text-align: center;
    line-height: 1.1;
  }
  .panel-heading .line-main { display: block; font-size: 18px; color: var(--heading); }
  .panel-heading .line-sub {
    display: flex; align-items: center; justify-content: center; gap: 8px;
    font-size: 18px; color: var(--heading-sub); margin-top: 2px;
  }
  .panel-heading .line-sub::before,
  .panel-heading .line-sub::after {
    content: ""; width: 20px; height: 1.5px; background: var(--heading-sub);
  }
  .field-label {
    display: block;
    font-family: "Cinzel", serif; font-weight: 700;
    font-size: 9px; letter-spacing: 0.3px;
    color: var(--label);
    margin: 0 0 5px 17px;
  }
  .form-field {
    position: relative;
    height: 43px;
    background: var(--field);
    display: flex; align-items: center;
    padding: 0 16px;
    font-size: 9px;
  }
  .form-field .value { color: var(--field-text); }
  .form-field .placeholder { color: var(--placeholder); }
  .form-field svg { position: absolute; right: 15px; top: 50%; transform: translateY(-50%); }
  .field-name { margin-top: 22px; }
  .field-group + .field-group { margin-top: 11px; }
  .description-field {
    margin-top: 13px;
    height: 72px;
    align-items: flex-start;
    padding-top: 15px;
  }
  .description-field svg { top: 14px; transform: none; }
  .submit-button {
    position: relative;
    margin-top: 13px;
    height: 43px;
    background: var(--button);
    display: flex; align-items: center; justify-content: center;
    font-family: "Cinzel", serif; font-weight: 700;
    font-size: 10.5px; color: var(--button-text);
  }
  .submit-button svg { position: absolute; right: 14px; top: 50%; transform: translateY(-50%); }
</style>
</head>
<body>
  <header class="brand">
    <span class="brand-mark"></span>
    <span class="brand-name">The Marlowe Crest<br>Advisory Services</span>
  </header>

  <section class="liaison-panel">
    <h1 class="panel-heading">
      <span class="line-main">Connect with a Liaison</span>
      <span class="line-sub">For Your Project</span>
    </h1>

    <div class="field-group field-name">
      <span class="field-label">Your Name*</span>
      <div class="form-field">
        <span class="value">jordan</span>
        <svg width="9" height="10" viewBox="0 0 9 10" fill="var(--icon)"><circle cx="4.5" cy="2.6" r="2.4"/><path d="M0 10c0-3 2-4.6 4.5-4.6S9 7 9 10z"/></svg>
      </div>
    </div>

    <div class="field-group">
      <span class="field-label">Your Email*</span>
      <div class="form-field">
        <span class="placeholder">info@mailhaven.com</span>
        <svg width="10" height="8" viewBox="0 0 10 8" fill="var(--icon)"><path d="M0 0h10v1.2L5 4.4 0 1.2z"/><path d="M0 2.4l5 3.2 5-3.2V8H0z"/></svg>
      </div>
    </div>

    <div class="field-group">
      <span class="field-label">Contact Info*</span>
      <div class="form-field">
        <span class="placeholder">555-014-782</span>
        <svg width="9" height="9" viewBox="0 0 9 9" fill="var(--icon)"><path d="M1.8 0.2l1.4 1.9-.9 1.1c.5 1.2 1.3 2 2.5 2.5l1.1-.9 1.9 1.4-.6 1.6C4 7.9 1.1 5 .2 1.2z"/></svg>
      </div>
    </div>

    <div class="form-field description-field">
      <span class="placeholder">Description of Project</span>
      <svg width="9" height="9" viewBox="0 0 9 9"><circle cx="4.5" cy="4.5" r="4.5" fill="var(--icon)"/><rect x="4" y="3.8" width="1.1" height="3.2" fill="var(--field)"/><circle cx="4.55" cy="2.5" r="0.65" fill="var(--field)"/></svg>
    </div>

    <div class="submit-button">
      Submit Request
      <svg width="11" height="11" viewBox="0 0 11 11" fill="var(--icon)"><path d="M11 0L0 4.6l3.3 1.4L9 1.8 4.3 6.8V11l2-2.4 2.3 1.2z"/></svg>
    </div>
  </section>
</body>
</html>
```